Luxury Wine Label for New Startup Winery

We need a wine label for our new winery startup. We have worked with a local designer but do not feel the resulting label / logo have the elevation required to present our brand as a luxury wine. Our winery is called "Quailbrook Vineyards" and we are focused on extremely high quality hand crafted artisan and estate wines from the Pacific Northwest.
We would like to see designs that utilize a tree line, or other imagery that represents the "Quailbrook" part of our company name. Another interesting feature could be wood grain.
A logo will be required based on your design so please design with this in mind:
This logo should be consistent with the wine bottle label design, and should be representative of our high end exclusive wine while giving a sense of place (Oregon/ Pacific Northwest.)
I will supply an image of the design we received from our local designer, PLEASE NOTE: in general we do like wood grain and tree line concepts but feel the execution was poorly done.
ATTN: Logo design should be suitable for use on: Bottles (Red wine/rose/white wine), Bussiness cards, vehicle signage, business signage, etc
P.S.:
If you have a design that is not outside the box we are still interested in seeing it.
Label is for a burgundy style bottle with a label height of 3.5 - 4" and a width of 3.5-4"
any label <= 4"x4" and >=3.5"x3.5" will be acceptable:
HOWEVER Width should be greater than or equal to height due to the bottle format
Target Market(s)
Wine enthusiasts with adequate discretionary budgets to afford $100 bottles of wine.
Industry/Entity Type
Wine / Winery
Requirements
Must have
- A sense of luxury, a feel of exclusivity, and a theme consistent with our product and brand name
Nice to have
- Tree line, wood grain or other wood themes. Serif fonts
Should not have
- anything cheesy, off topic, hard to read script fonts or anything that makes the label hard to read from a few feet away or too busy

```html
<!DOCTYPE html>
<html lang="en">
<head>
<meta charset="utf-8">
<title>Quailbrook Vineyards — Syrah Label</title>
<link rel="stylesheet" href="https://fonts.googleapis.com/css2?family=Tinos:wght@400;700&display=swap">
<style>
  :root {
    --paper: #ffffff;
    --label-black: #000000;
    --silver-dark: #5a5a5f;
    --silver-mid: #9a9aa0;
    --silver-light: #ececf0;
    --gold-dark: #5a3608;
    --gold-mid: #a97f2c;
    --gold-light: #f7ecb4;
    --wood-dark: #3e1c10;
    --wood-mid: #6e3523;
    --wood-light: #8c4a32;
    --ink-white: #ffffff;
  }
  html, body {
    margin: 0;
    padding: 0;
    width: 1112px;
    height: 1200px;
    overflow: hidden;
    background: var(--paper);
  }
  .canvas {
    position: relative;
    width: 1112px;
    height: 1200px;
    background: var(--paper);
    font-family: "Tinos", "Times New Roman", serif;
  }
  .silver-band {
    position: absolute;
    left: 0;
    width: 100%;
    height: 53px;
    background: linear-gradient(90deg, var(--silver-mid) 0%, var(--silver-light) 28%, var(--silver-light) 48%, var(--silver-mid) 70%, var(--silver-dark) 100%);
  }
  .gold-band {
    position: absolute;
    left: 0;
    width: 100%;
    height: 27px;
    background: linear-gradient(90deg, var(--gold-mid) 0%, var(--gold-light) 18%, var(--gold-mid) 40%, var(--gold-dark) 70%, var(--gold-mid) 100%);
  }
  .brand-label {
    position: absolute;
    left: 134px;
    top: 152px;
    width: 845px;
    height: 687px;
    background: var(--label-black);
  }
  .brand-label .silver-band.top { top: 0; }
  .brand-label .silver-band.bottom { bottom: 0; }
  .mountain-scene {
    position: absolute;
    left: 193px;
    top: 114px;
    width: 458px;
    height: 241px;
    background: radial-gradient(ellipse at 45% 55%, #c9a04a 0%, #8a6420 45%, rgba(0,0,0,0) 75%);
  }
  .wordmark {
    position: absolute;
    left: 0;
    width: 100%;
    margin: 0;
    text-align: center;
    white-space: nowrap;
  }
  .wordmark.name {
    top: 392px;
    font-size: 85px;
    font-weight: 700;
    letter-spacing: 8px;
    line-height: 1;
    background: linear-gradient(90deg, #4a4a50 0%, #8c8c92 25%, #f2f2f5 45%, #a5a5ab 65%, #55555b 100%);
    -webkit-background-clip: text;
    background-clip: text;
    color: transparent;
  }
  .wordmark.sub {
    top: 490px;
    font-size: 44px;
    font-weight: 400;
    letter-spacing: 25px;
    padding-left: 25px;
    line-height: 1;
    color: var(--ink-white);
  }
  .varietal-label {
    position: absolute;
    left: 134px;
    top: 865px;
    width: 845px;
    height: 185px;
  }
  .varietal-label .gold-band.top { top: 0; }
  .varietal-label .gold-band.bottom { bottom: 0; }
  .wood-panel {
    position: absolute;
    left: 0;
    top: 27px;
    width: 100%;
    height: 131px;
    background: linear-gradient(100deg, var(--wood-mid) 0%, var(--wood-light) 30%, var(--wood-mid) 55%, var(--wood-dark) 80%, var(--wood-mid) 100%);
  }
  .varietal-name {
    position: absolute;
    left: 0;
    top: 56px;
    width: 100%;
    margin: 0;
    text-align: center;
    font-size: 74px;
    font-weight: 700;
    letter-spacing: 5px;
    line-height: 1;
    color: var(--ink-white);
  }
</style>
</head>
<body>
  <main class="canvas">
    <section class="brand-label">
      <div class="silver-band top"></div>
      <div class="mountain-scene" role="img" aria-label="Gold foil illustration of mountain peaks above a line of evergreen trees"></div>
      <h1 class="wordmark name">QUAILBROOK</h1>
      <p class="wordmark sub">VINEYARDS</p>
      <div class="silver-band bottom"></div>
    </section>
    <section class="varietal-label">
      <div class="gold-band top"></div>
      <div class="wood-panel" role="img" aria-label="Walnut wood grain texture"></div>
      <h2 class="varietal-name">SYRAH</h2>
      <div class="gold-band bottom"></div>
    </section>
  </main>
</body>
</html>
```